New Business Card Design Project

Use the flyer uploaded and website www.brightoakbuilders.com for inspiration.
List Our Services on Backside of business cards
Marcus Delling
Harborline Builders Inc.
Licensed General Contractors
858-471-6093

Contact Information for Business Card

Use the flyer uploaded and website www.brightoakbuilders.com for inspiration. List Our Services on Backside of business cards Marcus Delling Harborline Builders Inc. Licensed General Contractors 858-471-6093

```html
<!DOCTYPE html>
<html lang="en">
<head>
<meta charset="utf-8">
<title>Harborline Builders – Business Cards</title>
<link href="https://fonts.googleapis.com/css2?family=Cinzel:wght@400;500&family=Montserrat:wght@400;500&display=swap" rel="stylesheet">
<style>
  :root {
    --stage: #2b2b2d;
    --card: #141416;
    --accent: #e3222b;
    --ink: #ffffff;
    --ink-soft: #d9d9d9;
  }
  * { box-sizing: border-box; margin: 0; padding: 0; }
  html, body {
    width: 1200px; height: 900px; overflow: hidden;
    background: var(--stage);
  }
  .stage {
    position: relative; width: 1200px; height: 900px;
  }
  .card {
    position: absolute; left: 260px; width: 680px; height: 390px;
    background: var(--card);
    border-left: 5px solid var(--accent);
    border-bottom: 5px solid var(--accent);
    box-shadow: 0 14px 30px rgba(0,0,0,.55);
    color: var(--ink);
    font-family: "Montserrat", sans-serif;
  }
  .card--services { top: 40px; }
  .card--contact { top: 470px; }

  .brand-name {
    font-family: "Cinzel", serif; font-weight: 400;
    color: var(--ink); letter-spacing: 1px; white-space: nowrap;
    display: flex; align-items: center; gap: 12px;
  }
  .brand-mark {
    width: 10px; height: 10px; background: var(--ink);
  }

  /* services side */
  .card--services .brand-name {
    position: absolute; top: 150px; left: 0; right: 0;
    justify-content: center; font-size: 34px;
  }
  .service-list {
    position: absolute; top: 245px; left: 0; right: 0;
    text-align: center; font-size: 17px; line-height: 1.75; color: var(--ink);
  }
  .service-list .sep { color: var(--accent); margin: 0 6px; }

  /* contact side */
  .card--contact .brand-name {
    position: absolute; top: 120px; left: 70px; font-size: 26px;
  }
  .contact-list {
    position: absolute; top: 205px; left: 70px;
    list-style: none; font-size: 16px; line-height: 1.9;
  }
  .contact-list li { display: flex; align-items: center; gap: 10px; }
  .contact-list svg { width: 14px; height: 14px; fill: var(--accent); flex: none; }
  .company-legal {
    position: absolute; top: 315px; left: 70px; font-size: 17px;
  }
  .person {
    position: absolute; top: 42px; right: 0; text-align: right;
    padding-right: 46px;
  }
  .person-name {
    font-family: "Cinzel", serif; font-weight: 500; font-size: 26px;
    color: var(--accent); letter-spacing: 1px;
  }
  .person-title { font-size: 15px; color: var(--ink-soft); margin-top: 2px; }
  .person-flag {
    position: absolute; top: 40px; right: 0; width: 22px; height: 34px;
    background: var(--accent);
  }
</style>
</head>
<body>
<main class="stage">

  <section class="card card--services" aria-label="Services side">
    <div class="brand-name"><span class="brand-mark"></span>Harborline Builders</div>
    <p class="service-list">
      Painting<span class="sep">•</span>Flooring<span class="sep">•</span>Kitchens<span class="sep">•</span>Custom Renovations<br>
      Bathrooms<span class="sep">•</span>Energy Efficienct Upgrades
    </p>
  </section>

  <section class="card card--contact" aria-label="Contact side">
    <span class="person-flag"></span>
    <div class="person">
      <p class="person-name">MARCUS DELLING</p>
      <p class="person-title">Licensed General Contractors</p>
    </div>

    <div class="brand-name"><span class="brand-mark"></span>Harborline Builders</div>

    <ul class="contact-list">
      <li>
        <svg viewBox="0 0 16 16" aria-hidden="true"><path d="M3.6 1.2 6 3.6 4.7 5.4c.8 1.9 2.1 3.2 4 4l1.8-1.3 2.4 2.4-1.6 2.3C6.7 12.6 3.4 9.3 1.3 2.8z"/></svg>
        858-471-6093
      </li>
      <li>
        <svg viewBox="0 0 16 16" aria-hidden="true"><path d="M1 3h14v10H1z M1 3l7 5 7-5" stroke="#141416" stroke-width="1"/></svg>
        info@brightoakbuilders.com
      </li>
      <li>
        <svg viewBox="0 0 16 16" aria-hidden="true"><circle cx="8" cy="8" r="7"/><path d="M1 8h14M8 1c3 3 3 11 0 14M8 1c-3 3-3 11 0 14" stroke="#141416" stroke-width="1" fill="none"/></svg>
        www.brightoakbuilders.com
      </li>
    </ul>

    <p class="company-legal">Harborline Builders Inc.</p>
  </section>

</main>
</body>
</html>
```